IT support company needs Banner Ad for the top of their quote layout template

We need a banner Ad for the top of our for quote layout template so it is sent out on all our quotes

The banner size must be 827 x 100 pixels - anything larger than 60 KB can cause upload time issues

We have attached our logo and examples of the quote page to see how it looks in the context of the whole page.

Essential elements of the banner
- Must have our logo but this can be changed to be different colours if it makes the design work better i.e. Kelmor Wave could be all in white

Colours
- Can use all of our standard colours - Orange, Black, Grey and White

Images
- As a premium IT support company we deal with people and technology so would like to see both of these Incorporated into the banner i.e. people using technology These images could be watermarked or one colour effect.

Look and Feel
- Professional, friendly, people, technology, premium

Target Market
Small business owners and managers

Industry/Entity Type

It Company

```html
<!DOCTYPE html>
<html lang="nl">
<head>
<meta charset="utf-8">
<title>Offerte TM-000280</title>
<link rel="stylesheet" href="https://fonts.googleapis.com/css2?family=Source+Sans+3:wght@400;600;700&display=swap">
<style>
  :root {
    --orange: #f26a1b;
    --orange-light: #f7931e;
    --orange-dark: #d9480f;
    --accent-text: #e2541a;
    --ink: #111111;
    --muted: #666666;
    --rule: #222222;
    --row-alt: #f2f2f2;
    --head-grey: #d9d9d9;
    --paper: #ffffff;
  }
  * { margin: 0; padding: 0; box-sizing: border-box; }
  html, body { width: 891px; height: 1200px; overflow: hidden; background: var(--paper); }
  body { font-family: "Source Sans 3", "Segoe UI", sans-serif; color: var(--ink); }
  .page {
    position: relative; width: 827px; height: 1114px;
    transform: scale(1.07739); transform-origin: 0 0;
  }
  .abs { position: absolute; }

  /* Banner */
  .banner {
    left: 0; top: 0; width: 827px; height: 104px;
    background: linear-gradient(90deg, var(--orange) 0%, var(--orange-light) 50%, var(--orange) 100%);
  }
  .banner-base { left: 0; top: 92px; width: 827px; height: 12px; background: var(--orange-dark); }
  .banner-people {
    left: 330px; top: 0; width: 240px; height: 92px;
    background: linear-gradient(90deg, rgba(217,72,15,0) 0%, rgba(217,72,15,.55) 40%, rgba(217,72,15,.55) 65%, rgba(217,72,15,0) 100%);
  }
  .brand-name {
    left: 28px; top: 34px; color: #fff; font-weight: 700; font-size: 34px;
    letter-spacing: 1px; line-height: 40px; text-transform: uppercase;
  }
  .banner-contact {
    right: 27px; top: 19px; text-align: right; color: #fff;
    font-size: 12.5px; font-weight: 600; line-height: 16px; opacity: .92;
  }

  .doc-title { left: 27px; top: 137px; font-size: 20px; line-height: 26px; }
  .portrait { left: 27px; top: 176px; width: 98px; height: 130px; background: linear-gradient(180deg, #9a9a9a, #4a4a4a); }
  .party { top: 174px; font-size: 13px; line-height: 17px; }
  .party h3 { color: var(--accent-text); font-size: 16px; font-weight: 600; line-height: 20px; margin-bottom: 5px; }
  .party strong { font-weight: 700; }
  .party p { margin-bottom: 3px; }
  .by { left: 135px; } .for { left: 360px; } .info { left: 627px; }

  .divider { left: 25px; top: 317px; width: 775px; height: 3px; background: var(--orange-dark); }

  .section-title { left: 27px; font-size: 17.5px; line-height: 22px; }

  .grid {
    position: absolute; left: 25px; width: 775px; border: 1px solid var(--rule);
    border-collapse: collapse; font-size: 12.5px;
  }
  .grid th {
    height: 24px; font-weight: 400; text-align: left; padding: 0 6px;
    background: linear-gradient(90deg, var(--head-grey), #f4f4f4 60%, var(--head-grey));
  }
  .grid td { height: 26px; padding: 0 6px; }
  .grid tr:nth-child(even) td { background: var(--row-alt); }
  .grid .num { text-align: right; border-left: 1px solid var(--rule); }
  .w-amount { width: 108px; }

  .sum { right: 31px; font-size: 13px; line-height: 16px; display: flex; gap: 0; }
  .sum .label { color: var(--muted); text-align: right; width: 300px; padding-right: 36px; }
  .sum .value { font-weight: 700; text-align: right; width: 72px; }
  .sum.optional .label { color: var(--accent-text); }

  .terms { left: 27px; top: 920px; font-size: 12.5px; }
  .sign-line { top: 992px; height: 1px; background: var(--rule); }
  .sign-label { top: 995px; font-size: 12.5px; }

  .footer-line { left: 0; top: 1068px; width: 827px; height: 4px; background: var(--orange); }
  .footer {
    left: 0; top: 1072px; width: 827px; height: 42px;
    background: linear-gradient(90deg, #e6e6e6, #ffffff 50%, #d0d0d0);
    display: flex; justify-content: space-between; align-items: center;
    padding: 0 27px; font-size: 12.5px;
  }
</style>
</head>
<body>
<div class="page">
  <header>
    <div class="abs banner"></div>
    <div class="abs banner-people" role="img" aria-label="Faint silhouettes of business people in front of a technology globe"></div>
    <div class="abs banner-base"></div>
    <div class="abs brand-name">Kelmor Wave</div>
    <address class="abs banner-contact" style="font-style:normal">
      Alder House, Millbrook Lane, Harlow Fen<br>
      Wickford Vale, Norfolk, NR19 4LT<br>
      www.kelmorwave.co.uk<br>
      01702 558190
    </address>
  </header>

  <h1 class="abs doc-title" style="font-weight:400">Standard MSP&nbsp; #2</h1>
  <div class="abs portrait" role="img" aria-label="Portrait photo of the quote author"></div>

  <section class="abs party by">
    <h3>Opgesteld door:</h3>
    <p><strong>Tom Marlow Ltd</strong></p>
    <p>Tom Marlow</p>
    <p>&nbsp;</p>
    <p style="margin-bottom:0">Fax</p>
    <p>tom.marlow@quotepine.com</p>
  </section>
  <section class="abs party for">
    <h3>Opgesteld voor:</h3>
    <p><strong>Grey Ridge</strong></p>
    <p style="margin-bottom:0">2817 Lantern Ave.</p>
    <p style="margin-bottom:0">Fairhaven,&nbsp;&nbsp; 48231</p>
    <p style="margin-bottom:0">Rosalind Park</p>
    <p>ben.carver@bluefinch.co.uk</p>
  </section>
  <section class="abs party info">
    <h3>Gegevens Offerte:</h3>
    <p><strong>Offerte #: TM-000280</strong></p>
    <p>Versie: 1</p>
    <p style="margin-bottom:0">Leverdatum: 14/11/2017</p>
    <p>Vervaldatum: 31/12/2017</p>
  </section>

  <div class="abs divider"></div>

  <h2 class="abs section-title" style="top:338px;font-weight:400">Overzicht Offerte</h2>
  <table class="grid" style="top:366px">
    <tr><th>Beschrijving</th><th class="num w-amount">Bedrag</th></tr>
    <tr><td>Initial Investment</td><td class="num">$800.00</td></tr>
  </table>
  <div class="abs sum" style="top:425px"><span class="label">Subtotaal:</span><span class="value">$800.00</span></div>
  <div class="abs sum" style="top:450px"><span class="label">VAT:</span><span class="value">$160.00</span></div>
  <div class="abs sum" style="top:475px"><span class="label">Totaal:</span><span class="value">$960.00</span></div>

  <h2 class="abs section-title" style="top:515px;font-weight:400">Overzicht Terugkerende Kosten</h2>
  <table class="grid" style="top:542px">
    <tr><th>Beschrijving</th><th class="num w-amount">Bedrag</th></tr>
    <tr><td>Monitoring</td><td class="num">$375.00</td></tr>
    <tr><td>Support</td><td class="num">$65.00</td></tr>
    <tr><td>Fixed Hours</td><td class="num">$850.00</td></tr>
  </table>
  <div class="abs sum" style="top:653px"><span class="label">Terugkerende totaal:</span><span class="value">$1,290.00</span></div>

  <h2 class="abs section-title" style="top:693px;font-weight:400">*Optionele kosten</h2>
  <table class="grid" style="top:720px">
    <tr><th>Beschrijving</th><th class="num w-amount">Recurring</th><th class="num w-amount">One-Time</th></tr>
    <tr><td>Monitoring</td><td class="num">$790.00</td><td class="num">$0.00</td></tr>
    <tr><td>Support</td><td class="num">$185.00</td><td class="num">$0.00</td></tr>
    <tr><td>Fixed Hours</td><td class="num">$695.00</td><td class="num">$0.00</td></tr>
    <tr><td>Add-on Services</td><td class="num">$850.00</td><td class="num">$0.00</td></tr>
  </table>
  <div class="abs sum optional" style="top:858px"><span class="label">Optionele terugkerend bedrag:</span><span class="value">$2,520.00</span></div>
  <div class="abs sum optional" style="top:883px"><span class="label">Optionele ongeplande Subtotaal:</span><span class="value">$.00</span></div>

  <p class="abs terms">Taxes, shipping, handling and other fees may apply.&nbsp; We reserve the right to cancel orders arising from pricing or other errors.</p>

  <div class="abs sign-line" style="left:25px;width:464px"></div>
  <div class="abs sign-line" style="left:518px;width:182px"></div>
  <span class="abs sign-label" style="left:27px">Handtekening</span>
  <span class="abs sign-label" style="left:520px">Datum</span>

  <div class="abs footer-line"></div>
  <footer class="abs footer">
    <span>Offerte #TM-000280 v1</span>
    <span>Pagina 6 Van 7</span>
  </footer>
</div>
</body>
</html>
```